Catalogue Design Project

We need a catalog design for a new private university called Redwell Institute Bayshore (see website www.rwi-bs.org). The catalog should be about 30 pages maximum and will include items such as General Information, Academic schedule, department descriptions, program descriptions, course descriptions, school policies, student services, admissions, San diego Lifestyle, etc.
I will provide the text but I need a professional design with regard to page layouts. I have provided some examples.
Ok, i posted the catalog content, just missing course descriptions.
Target Market(s)
Young Professionals, Foreign Students
Industry/Entity Type
University
Look and feel
Each slider illustrates characteristics of the customer's brand and the style your logo design should communicate.

```html
<!DOCTYPE html>
<html lang="en">
<head>
<meta charset="utf-8">
<title>University Policies – Redwell Institute Bayshore Catalogue</title>
<link href="https://fonts.googleapis.com/css2?family=Carlito:wght@400;700&display=swap" rel="stylesheet">
<style>
  :root {
    --navy: #1f4f82;
    --navy-light: #5b84b1;
    --ink: #1a1a1a;
    --rule: #8aa6c4;
    --row-dark: #d8d3d6;
    --row-light: #f3eef0;
    --table-edge: #3a3a3a;
    --muted: #8a8f96;
    --photo-a: #ffffff;
    --photo-b: #dfe7ef;
  }
  * { margin: 0; padding: 0; box-sizing: border-box; }
  html, body { width: 927px; height: 1200px; overflow: hidden; background: #fff; }
  body { font-family: "Carlito", "Calibri", sans-serif; color: var(--ink); }
  .page { position: relative; width: 927px; height: 1200px; overflow: hidden; }

  .header-photo {
    position: absolute; right: 0; top: 0; width: 330px; height: 103px;
    background: linear-gradient(100deg, var(--photo-a) 0%, var(--photo-b) 60%, #c9d6e3 100%);
  }
  .brand {
    position: absolute; left: 58px; top: 30px; display: flex; align-items: center; gap: 10px;
    font-size: 17px; font-weight: 700; color: var(--navy);
  }
  .brand-dot { width: 16px; height: 16px; border-radius: 50%; background: var(--navy); }
  .header-band { position: absolute; left: 0; top: 100px; width: 927px; height: 42px; }
  .section-tab {
    position: absolute; right: 22px; top: 106px; color: #fff;
    font-size: 29px; letter-spacing: 0.5px; line-height: 32px;
  }

  .page-title {
    position: absolute; left: 0; width: 927px; top: 148px; text-align: center;
    font-size: 26px; font-weight: 700;
  }
  .block {
    position: absolute; left: 80px; width: 803px;
    font-size: 17px; line-height: 27px; text-align: justify;
  }
  .block h2 { font-size: 17px; font-weight: 400; text-decoration: underline; }
  .tuition { top: 181px; }
  .dropping { top: 606px; }
  .dropping .lead-in { line-height: 29px; }
  .grading { top: 966px; }

  .data-table {
    position: absolute; left: 80px; border: 1.5px solid var(--table-edge);
    box-shadow: 1px 1px 2px rgba(0,0,0,0.35); font-size: 16.5px;
  }
  .data-table .row { display: flex; align-items: center; padding-left: 16px; }
  .data-table .row:nth-child(odd) { background: var(--row-dark); }
  .data-table .row:nth-child(even) { background: var(--row-light); }
  .fees { top: 291px; width: 475px; }
  .fees .row { height: 22px; }
  .fees .label { width: 364px; }
  .refunds { top: 851px; width: 242px; }
  .refunds .row { height: 22px; }
  .refunds .label { width: 146px; }
  .grades { top: 991px; width: 240px; }
  .grades .row { height: 22.6px; }
  .grades .label { width: 92px; }

  .footer-rule { position: absolute; left: 0; top: 1155px; width: 927px; height: 2px; background: var(--rule); }
  .folio {
    position: absolute; right: 44px; top: 1172px; font-size: 12.5px; color: var(--muted); letter-spacing: 0.3px;
  }
</style>
</head>
<body>
<main class="page">
  <div class="header-photo" role="img" aria-label="Soft faded photograph of a graduation scene in pale blue tones"></div>
  <div class="brand"><span class="brand-dot"></span>Redwell Institute Bayshore</div>

  <svg class="header-band" viewBox="0 100 927 42" width="927" height="42" aria-hidden="true">
    <rect x="0" y="102" width="927" height="2" fill="var(--navy-light)"/>
    <polygon points="560,102 927,102 927,140 584,140" fill="var(--navy-light)"/>
    <polygon points="574,104 927,104 927,140 598,140" fill="var(--navy)"/>
  </svg>
  <div class="section-tab">UNIVERSITY POLICIES</div>

  <h1 class="page-title">University Policies</h1>

  <section class="block tuition">
    <h2>Tuition &amp; Fees</h2>
    <p>Tuition must be paid during the grace period which ends exactly one week from the first of every month. Tuition paid after the grace period will be assessed a late tuition fee.</p>
    <p>The following is a list of university tuition costs and related fees:</p>
  </section>

  <div class="data-table fees">
    <div class="row"><span class="label">Application</span><span>$60.00</span></div>
    <div class="row"><span class="label">MBA/Certificate 3 Unit Course</span><span>$800.00</span></div>
    <div class="row"><span class="label">TESOL Certificate</span><span>$550.00</span></div>
    <div class="row"><span class="label">Starting Your Own Business Certificate</span><span>$550.00</span></div>
    <div class="row"><span class="label">Audit Preparation Certicate</span><span>$400.00</span></div>
    <div class="row"><span class="label">Ledgerline Certicate</span><span>$200.00</span></div>
    <div class="row"><span class="label">ESL</span><span>$300.00</span></div>
    <div class="row"><span class="label">Import/Export Certifiate</span><span>$400.00</span></div>
    <div class="row"><span class="label">Late Registration Fee</span><span>$20.00</span></div>
    <div class="row"><span class="label">Late Drop Fee</span><span>$15.00</span></div>
    <div class="row"><span class="label">Late Add Fee</span><span>$15.00</span></div>
    <div class="row"><span class="label">Official Transcript</span><span>$10.00</span></div>
    <div class="row"><span class="label">Late Tuition Fee</span><span>$15.00</span></div>
  </div>

  <section class="block dropping">
    <h2>Dropping and Adding Courses / Refund Policy</h2>
    <p>The official add/drop period deadline is the last day of the first week of class.&nbsp; Before the deadline, students can drop or add without any financial penalty.&nbsp; After the deadline and before the 3rd week of class, a student will be responsible for paying a late drop or add fee.&nbsp; In the event of a late add, the student must have the approval from the instructor of the added class.&nbsp; Students who drop classes up until the third week and choose not to add another class or withdraw, are eligible for tuition refund.&nbsp; Classes dropped after the third week or not eligible for a refund.&nbsp; Additionally, classes dropped will be listed as DC (dropped course) on official transcripts.</p>
    <p class="lead-in">The following is the refund schedule for an 8 week course.</p>
  </section>

  <div class="data-table refunds">
    <div class="row"><span class="label">Week 1</span><span>$800.00</span></div>
    <div class="row"><span class="label">Week 2</span><span>$700.00</span></div>
    <div class="row"><span class="label">Week 3</span><span>$600.00</span></div>
    <div class="row"><span class="label">After Week 3</span><span>N/A</span></div>
  </div>

  <section class="block grading">
    <h2>Grading</h2>
  </section>

  <div class="data-table grades">
    <div class="row"><span class="label">A</span><span>4</span></div>
    <div class="row"><span class="label">A-</span><span>3.67</span></div>
    <div class="row"><span class="label">B+</span><span>3.33</span></div>
    <div class="row"><span class="label">B</span><span>3</span></div>
    <div class="row"><span class="label">F</span><span>Fail</span></div>
    <div class="row"><span class="label">DC</span><span>Dropped Course</span></div>
  </div>

  <div class="footer-rule"></div>
  <div class="folio">20::: REDWELL INSTITUTE</div>
</main>
</body>
</html>
```